Laser Tattoo Removal Business Cards

We are looking for a professional business card design for a laser tattoo removal business. Ideally looking for a black business card design. The name of the business is Palewick Tattoo Removal. We place our cards at local tattoo shops so we ideally are looking for something trendy/edgy to draw both male and female clientele in.

Target Market(s)

Male/Female ages 18-60

Contact Information for Business Card

black background ideally.. hoping to stay within greys, whites and black

Font styles to use
Serif
Sans Serif

Colors
121212
a9a9a9
5c5c5c
f5f5f5
ffffff
7f7f7f
606060
848484
9d9d9d

Requirements
Must have
• Employee Info:
• Melissa Thornbury
• Chief Executive Offer
• m: 919.537.2846
• w: 919.362.4178
• f: 919.685.3907
• mthornbury@palewicktattooremoval.example
• Address:
• 4615 Oakmere Pkwy, Suite 210
• Raleigh, NC 27654
• Website:
• www.palewicktattooremoval.example
Nice to have
• Myabe business name on back or logo on back and employee info on the front

```html
<!DOCTYPE html>
<html lang="en">
<head>
<meta charset="utf-8">
<title>Palewick Tattoo Removal – Business Cards</title>
<link rel="stylesheet" href="https://fonts.googleapis.com/css2?family=Arimo:wght@400;700&display=swap">
<style>
  :root {
    --ink: #121212;
    --charcoal: #2a2a2a;
    --grey-dark: #5c5c5c;
    --grey-mid: #7f7f7f;
    --grey-light: #a9a9a9;
    --paper: #f5f5f5;
    --white: #ffffff;
    --backdrop: #d9d9d9;
  }
  * { margin: 0; padding: 0; box-sizing: border-box; }
  html, body { width: 1200px; height: 886px; overflow: hidden; }
  body { background: var(--backdrop); position: relative; font-family: Arimo, sans-serif; }

  .card {
    position: absolute;
    top: 110px;
    width: 380px;
    height: 665px;
    overflow: hidden;
    box-shadow: 0 8px 24px rgba(0,0,0,0.25);
  }
  .card--front { left: 180px; background: var(--charcoal); }
  .card--back { left: 640px; background: var(--ink); }

  .front-shape { position: absolute; inset: 0; width: 380px; height: 665px; }

  .brand {
    position: absolute;
    left: 0; right: 0;
    display: flex;
    align-items: center;
    justify-content: center;
    gap: 10px;
    font-family: Arimo, sans-serif;
    font-weight: 400;
    font-size: 25px;
    white-space: nowrap;
  }
  .brand-dot { width: 12px; height: 12px; border-radius: 50%; background: currentColor; flex: none; }
  .card--front .brand { top: 150px; color: var(--ink); }
  .card--back .brand { top: 316px; color: var(--white); }

  .contact {
    position: absolute;
    left: 30px;
    right: 30px;
    top: 400px;
    text-align: right;
    color: var(--white);
    font-size: 14px;
    line-height: 1.45;
  }
  .contact-name { font-weight: 700; font-size: 19px; letter-spacing: 0.5px; text-transform: uppercase; }
  .contact-role { margin-bottom: 12px; font-size: 15px; }
  .contact-block { margin-bottom: 10px; }
</style>
</head>
<body>
  <section class="card card--front" aria-label="Business card front">
    <svg class="front-shape" viewBox="0 0 380 665" aria-hidden="true">
      <path d="M0 0 H380 V345 Q190 250 0 300 Z" fill="var(--white)"/>
      <path d="M30 322 Q210 275 380 368" fill="none" stroke="var(--white)" stroke-width="2.5"/>
    </svg>
    <div class="brand"><span class="brand-dot"></span><span class="brand-name">Palewick Tattoo Removal</span></div>
    <div class="contact">
      <div class="contact-name">Melissa Thornbury</div>
      <div class="contact-role">Chief Executive Offer</div>
      <div class="contact-block">4615 Oakmere Pkwy, Suite 210<br>Raleigh, NC 27654</div>
      <div>P: 919.362.4178</div>
      <div>M: 919.537.2846 &nbsp;F: 919.685.3907</div>
      <div>mthornbury@palewicktattooremoval.example</div>
      <div>www.palewicktattooremoval.example</div>
    </div>
  </section>

  <section class="card card--back" aria-label="Business card back">
    <div class="brand"><span class="brand-dot"></span><span class="brand-name">Palewick Tattoo Removal</span></div>
  </section>
</body>
</html>
```